Website Design Needed for Performance Horse Trading Business

We require a website designed for Saddlewend, a new business which lists top quality performance stock horse bloodlines for sale. Our Australian company caters to the Australian Stock Horse, Quarter Horse and Paint Horse breeds of horse used for performance events such as Camp drafting and Cutting. The website design needs to communicate quality, have a professional look while maintaining a western, rural feel.
Colour schemes that we are looking for are either grey and orange, navy and grey or brown and grey.
The logo for the website has been attached below
Design deliverables are as follows:
-Main Page
-Horses for Sale Page
-Horse Listing Page
-Html & CSS files for pages
MAIN PAGE
----------------
Description: This page is where customers land, search for horses, see premium horses
Elements which need to be included on the main page are
-a horse filter section, allowing customers to search for horse listings by filtering attributes.
-premium listings displaying large photos of horse, price and location.
Horses for Sale PAGE
---------------------------------
Description: This page displays a list of available horses for sale as per the filtered results.
Elements which need to be included on this page are
- a filter panel which allows customers to filter results
- list of horses available for sale
Horse Listing Page
-------------------------------
Description: This page displays all the information about the horse for sale.
Screenshots of the basic program are attached for the Horses for Sale Page and the Horse Listing Page to give an idea of the elements required ONLY and should not be thought of as a design guideline.
Webpage HEADER
-------------------------
The Header section of the website should include login/signup buttons, 'my account' buttons (or links) as well as a featured link/button that says 'Sell Your Horse'
Updates
Thank you all for your designs so far. We would like to see the Sell Your Horse section featured more in the website design to attract customers. This would be as a button or highlighted link that is eye catching in the primary section of the website design of the main page. Perhaps placing it on the right hand side adjacent to the search function lets customers make the mental decision as to whether they are looking to buy or looking to sell when they visit the website. The wording above or near the button would be 'Advertise your horse with us' with the words on the button being 'Create Ad!'.
Industry/Entity Type
Events
Look and feel
Each slider illustrates characteristics of the customer's brand and the style your logo design should communicate.

```html
<!DOCTYPE html>
<html lang="en">
<head>
<meta charset="utf-8">
<title>Saddlewend – Performance Horses</title>
<link rel="stylesheet" href="https://fonts.googleapis.com/css2?family=Raleway:wght@300;400&family=Roboto+Condensed:wght@400;700&family=Roboto:wght@300;400&display=swap">
<style>
:root{
  --ink:#0b0b0b;
  --bar:#151515;
  --bar-btn:#1f1f1f;
  --accent:#ef6650;
  --tile:#ee6b55;
  --panel:#efefef;
  --soft:#f4f4f4;
  --text:#333;
  --muted:#8a8a8a;
  --footer:#1c1c1c;
  --white:#fff;
}
*{box-sizing:border-box;margin:0;padding:0}
html,body{width:807px;height:1200px;overflow:hidden;background:var(--white)}
body{position:relative;font-family:'Roboto',sans-serif;color:var(--text)}
.abs{position:absolute}
.cond{font-family:'Roboto Condensed',sans-serif}
.rale{font-family:'Raleway',sans-serif;font-weight:300}

.hero{left:0;top:0;width:807px;height:524px;background:var(--ink)}
.hero-photo{left:392px;top:52px;width:415px;height:420px;
  background:radial-gradient(ellipse at 55% 45%,#b8743a 0%,#8a4f22 35%,#3a2010 65%,rgba(11,11,11,0) 85%)}
.topbar{left:0;top:0;width:807px;height:22px;background:var(--bar)}
.topbar a{position:absolute;top:0;height:22px;line-height:22px;text-align:center;font-size:7.5px;color:#ccc;text-decoration:none;background:var(--bar-btn);border-left:1px solid #000}
.topbar a.sell{background:var(--accent);color:var(--white)}

.brand{left:60px;top:28px;color:var(--white);font-family:'Roboto Condensed',sans-serif;font-weight:700;font-size:25px;letter-spacing:1px}
.brand-sub{left:84px;top:58px;color:var(--white);font-size:5px;letter-spacing:10px}
.nav{left:60px;top:81px;display:flex;font-family:'Roboto Condensed',sans-serif;font-size:9.5px}
.nav span{color:var(--white);padding:0 7px;border-left:1px dotted #777;line-height:12px}
.nav span:first-child{border:0;padding-left:0;color:var(--accent)}

.headline{left:79px;top:186px;font-size:35px;line-height:36px;color:var(--white)}
.headline em{font-style:normal;color:var(--accent);display:block}
.hero-copy{left:79px;top:270px;width:300px;font-size:7.5px;line-height:10px;color:#ddd}
.know{left:78px;top:316px;width:80px;height:22px;border-radius:11px;background:#3d3d3d;color:#ccc;font-size:7px;line-height:22px;text-align:center}

.search{left:74px;top:381px;width:660px;height:49px;background:#2b2b2b;padding:5px}
.search-in{position:relative;width:100%;height:100%;background:#141414}
.search-label{left:0;top:0;width:130px;height:39px;background:#000;color:var(--white);font-size:13px;line-height:39px;padding-left:24px;clip-path:polygon(0 0,90% 0,100% 50%,90% 100%,0 100%)}
.field{top:11px;height:21px;background:var(--white);font-size:8.5px;color:#aaa;line-height:21px;padding-left:8px}
.go{top:11px;left:477px;width:161px;height:21px;background:var(--accent);color:var(--white);font-size:9px;line-height:21px;text-align:center}

.premium{left:58px;top:430px;width:692px;height:266px;background:var(--panel);box-shadow:0 6px 8px -6px rgba(0,0,0,.25)}
.premium h2{position:absolute;left:0;right:0;top:20px;text-align:center;font-size:21px;color:#555}
.card{top:64px;width:203px;height:172px;background:var(--white)}
.card .pic{height:128px}
.card .name{position:absolute;left:6px;top:134px;font-size:10px;color:#444}
.card .meta{position:absolute;left:6px;top:152px;right:4px;font-size:6.8px;color:#999;display:flex;align-items:baseline}
.card .meta b{font-weight:400;color:var(--accent);font-size:10px;margin:0 29px 0 4px}
.card .meta i{font-style:normal;color:#444;margin-left:3px}
.dots{left:0;right:0;top:247px;display:flex;justify-content:center;gap:7px}
.dots i{width:5px;height:5px;border-radius:50%;background:#bbb}
.dots i:first-child{background:var(--accent)}

.welcome{left:0;top:728px;width:807px;height:236px;background:var(--soft)}
.horse-art{left:52px;top:24px;width:204px;height:200px;background:radial-gradient(ellipse at 55% 45%,#9a5426 0%,#7a3f1c 40%,rgba(244,244,244,0) 70%)}
.w-title{left:276px;top:34px;font-size:21px;line-height:24px;color:#333}
.w-title em{font-style:normal;color:var(--accent);display:block}
.w-copy{left:276px;top:93px;width:230px;font-size:8.3px;line-height:11px;color:var(--muted)}
.read{left:275px;top:150px;width:87px;height:26px;background:var(--accent);color:var(--white);font-size:8.5px;line-height:26px;text-align:center}
.news-title{left:546px;top:36px;font-size:21px;color:#333}
.news-title em{font-style:normal;color:var(--accent)}
.news{left:546px;width:200px;font-size:8.3px;color:var(--muted);line-height:11px}
.news .date{color:var(--accent);font-size:10px;font-family:'Roboto Condensed',sans-serif}
.news .head{color:#333;font-size:10px;margin:2px 0 4px}
.news.first{border-bottom:1px solid #e0e0e0;padding-bottom:10px}

.breeds{left:58px;top:994px;width:692px;height:102px;display:flex}
.breed{width:230.7px;height:102px;display:flex;background:var(--tile)}
.breed .pic{width:91px;height:102px}
.breed .txt{padding:13px 0 0 12px;color:var(--white)}
.breed h3{font-family:'Roboto Condensed',sans-serif;font-weight:400;font-size:16px;line-height:17px}
.breed p{font-family:'Roboto Condensed',sans-serif;font-size:7px;line-height:9.5px;margin-top:8px}
.breed .more{font-family:'Roboto Condensed',sans-serif;font-style:italic;font-size:7.5px;margin-top:8px}

.footer{left:0;top:1128px;width:807px;height:72px;background:var(--footer);font-family:'Roboto Condensed',sans-serif;color:#999}
.f-links{left:54px;top:22px;font-size:8.5px}
.f-copy{left:54px;top:39px;font-size:8.5px}
.news-label{left:278px;top:21px;font-size:8.5px}
.mail{left:278px;top:36px;width:102px;height:16px;background:#3a3a3a;font-size:7px;color:#888;line-height:16px;padding-left:7px}
.sub{left:380px;top:36px;width:46px;height:16px;background:var(--accent);font-size:7px;color:var(--white);line-height:16px;text-align:center}
.call{left:478px;top:22px}
.call-label{left:510px;top:22px;font-size:7.5px}
.call-num{left:510px;top:32px;font-size:13px;color:#ccc}
.social{left:653px;top:23px;display:flex;gap:5px}
.social i{width:19px;height:19px;border-radius:50%;background:#3a3a3a}
</style>
</head>
<body>

<section class="hero abs">
  <div class="hero-photo abs" role="img" aria-label="Photo of a bay horse's head wearing a halter"></div>

  <div class="topbar abs">
    <a style="left:510px;width:46px">LOGIN</a>
    <a style="left:556px;width:46px">SIGNUP</a>
    <a style="left:602px;width:66px">MY ACCOUNT</a>
    <a class="sell" style="left:668px;width:82px">SELL YOUR HORSE</a>
  </div>

  <div class="brand abs">SADDLEWEND</div>
  <div class="brand-sub abs">AUSTRALIA</div>

  <nav class="nav abs">
    <span>Home</span><span>About Us</span><span>For Sale</span><span>Gallery</span><span>Events</span><span>Contacts</span>
  </nav>

  <h1 class="headline rale abs">Camp Drafting<em>and Cutting</em></h1>
  <p class="hero-copy abs">Praesent vestibulum molestie lacus. Aenean nonummy hendrerit mauris. Phasellus porta. Fusce suscipit varius mi. Cum sociis natoque penatibus et magnis dis parturient montes, nascetur ridiculus mus.</p>
  <div class="know cond abs">KNOW MORE</div>
</section>

<form class="search abs">
  <div class="search-in">
    <div class="search-label cond abs">Search Horses</div>
    <div class="field cond abs" style="left:146px;width:160px">Category
      <svg class="abs" style="right:0;top:0" width="20" height="21"><line x1="0.5" y1="3" x2="0.5" y2="18" stroke="#ddd"/><path d="M7 9l3 3 3-3" fill="none" stroke="#999" stroke-width="1"/></svg>
    </div>
    <div class="field cond abs" style="left:315px;width:161px">Keywords</div>
    <div class="go cond abs">SEARCH</div>
  </div>
</form>

<section class="premium abs">
  <h2 class="rale">Premium Horses</h2>
  <article class="card abs" style="left:22px">
    <div class="pic" role="img" aria-label="Photo of a herd of horses running through dry grass" style="background:linear-gradient(#d9b574,#7a3a22 55%,#c9a35c)"></div>
    <div class="name cond">Miuyase Consrtsera</div>
    <div class="meta cond">PRICE:<b>$256</b>LOCATION:<i>NERAFAES LASERTYUS</i></div>
  </article>
  <article class="card abs" style="left:248px">
    <div class="pic" role="img" aria-label="Photo of a chestnut horse with a pale mane in a halter" style="background:linear-gradient(135deg,#6b3b28,#9a5a3c 50%,#5f6b3a)"></div>
    <div class="name cond">Miuyase Consrtsera</div>
    <div class="meta cond">PRICE:<b>$256</b>LOCATION:<i>NERAFAES LASERTYUS</i></div>
  </article>
  <article class="card abs" style="left:469px">
    <div class="pic" role="img" aria-label="Photo of a pale horse grazing in a green field" style="background:linear-gradient(#7d8a45,#cfc6b0 50%,#6e7d34)"></div>
    <div class="name cond">Miuyase Consrtsera</div>
    <div class="meta cond">PRICE:<b>$256</b>LOCATION:<i>NERAFAES LASERTYUS</i></div>
  </article>
  <div class="dots abs"><i></i><i></i><i></i><i></i></div>
</section>

<section class="welcome abs">
  <div class="horse-art abs" role="img" aria-label="Photo of a chestnut horse trotting"></div>
  <h2 class="w-title rale abs">Welcome to<em>Saddlewend</em></h2>
  <p class="w-copy abs">Meciegast niversta senterta dausya saeitset ertplica. Maselementum ursus eleifender. Aenean auctor wisi et urna. Viliquam erat volutpas matsreuisac turpilnter rutrum anteulacus.</p>
  <div class="read cond abs">READ MORE</div>

  <h2 class="news-title rale abs">Latest <em>News</em></h2>
  <div class="news first abs" style="top:70px">
    <div class="date">27-10</div>
    <div class="head">Besrtasa Fertasade</div>
    Meciegast niversta senterta dausya saeitset ertplica.Maselementum ursus eleifender.
  </div>
  <div class="news abs" style="top:143px">
    <div class="date">27-10</div>
    <div class="head">Besrtasa Fertasade</div>
    Meciegast niversta senterta dausya saeitset ertplica.Maselementum ursus eleifender.
  </div>
</section>

<section class="breeds abs">
  <article class="breed">
    <div class="pic" role="img" aria-label="Photo of an Australian Stock Horse in a paddock" style="background:linear-gradient(#4d7a34,#b0703e 50%,#5a8a3a)"></div>
    <div class="txt"><h3>Australian Stock Horse</h3><p>Casuptate uisagni ahseoquies dolo-<br>res nesciunt</p><div class="more">MORE</div></div>
  </article>
  <article class="breed">
    <div class="pic" role="img" aria-label="Photo of two Quarter Horses side by side" style="background:linear-gradient(135deg,#9a5a30,#c98a52 50%,#6b3a20)"></div>
    <div class="txt"><h3 style="margin-top:9px">Quarter Horse</h3><p style="margin-top:10px">Casuptate uisagni ahseoquies dolo-<br>res nesciunt</p><div class="more">MORE</div></div>
  </article>
  <article class="breed">
    <div class="pic" role="img" aria-label="Photo of a spotted Paint Horse standing on grass" style="background:linear-gradient(#6a8a4a,#d8d0c8 45%,#7a9a52)"></div>
    <div class="txt"><h3>Paint Horse Breeds</h3><p>Casuptate uisagni ahseoquies dolo-<br>res nesciunt</p><div class="more">MORE</div></div>
  </article>
</section>

<footer class="footer abs">
  <div class="f-links abs">About &nbsp;|&nbsp; Terms &nbsp;|&nbsp; Privacy Policy</div>
  <div class="f-copy abs">All Rights Reserved. Copyrights © 2014.</div>
  <div class="news-label abs">Newsletter Signup</div>
  <div class="mail abs">Email Address</div>
  <div class="sub abs">Subscribe</div>
  <svg class="call abs" width="27" height="27" viewBox="0 0 27 27">
    <circle cx="13.5" cy="13.5" r="12.5" fill="none" stroke="#666" stroke-width="1.5"/>
    <path d="M9 7.5c1-.8 2 .2 2.6 1.6.4 1 0 1.5-.6 2-.4.3-.2 1 .6 2.2s1.6 1.8 2.1 1.5c.7-.5 1.3-.9 2.2-.3 1.2.8 2 1.7 1 2.7-1.6 1.6-4.2.5-6.4-2.2S7.4 9 9 7.5z" fill="#777"/>
  </svg>
  <div class="call-label abs">Call Us:</div>
  <div class="call-num abs">041-2207-3316</div>
  <div class="social abs" aria-label="Social links"><i></i><i></i><i></i><i></i></div>
</footer>

</body>
</html>
```